Business card for law firm

Need business card for new law firm. Think confident, authoritative, conservative, but not stuffy or old-fashioned.

Contact Information for Business Card

Content for card - logo (uploaded), plus the following:

Paul Whitcombe (larger font)
Managing Partner (larger font, but not as large as name)
Level 9, 7 Ferris Lane
Sydney NSW 2000
Main Tel 02 9364 2710
Direct Tel 02 8472 3159
Email paul@qvlegal.com.au
www.qvlegal.com.au

Letterhead design should include logo plus:
Level 9, 7 Ferris Lane
Sydney NSW 2000
Tel 02 8472 3159
www.qvlegal.com.au

```html
<!DOCTYPE html>
<html lang="en">
<head>
<meta charset="utf-8">
<title>Quayview Legal – Business Card</title>
<link rel="stylesheet" href="https://fonts.googleapis.com/css2?family=Marcellus&family=Jost:wght@400;600;700&display=swap">
<style>
  :root {
    --navy: #0f2060;
    --navy-deep: #0b1a4f;
    --paper: #e9e9ea;
    --ink: #1b1b1f;
    --rule: #3a3a40;
    --white: #ffffff;
    --backdrop: #3b3b3e;
  }
  * { box-sizing: border-box; margin: 0; padding: 0; }
  html, body {
    width: 1200px;
    height: 1000px;
    overflow: hidden;
    background: var(--backdrop);
  }
  .canvas {
    position: relative;
    width: 1200px;
    height: 1000px;
  }
  .card {
    position: absolute;
    width: 640px;
    height: 390px;
    border-radius: 26px;
    box-shadow: 0 14px 30px rgba(0, 0, 0, 0.35);
  }
  .card--front {
    left: 330px;
    top: 60px;
    background: linear-gradient(135deg, var(--navy) 0%, var(--navy-deep) 100%);
    color: var(--white);
    display: flex;
    flex-direction: column;
    align-items: center;
    justify-content: center;
  }
  .card--back {
    left: 230px;
    top: 520px;
    background: var(--paper);
    color: var(--ink);
  }
  .wordmark {
    display: flex;
    flex-direction: column;
    align-items: center;
    gap: 22px;
  }
  .wordmark__square {
    width: 58px;
    height: 58px;
  }
  .wordmark__name {
    font-family: "Marcellus", serif;
    font-size: 44px;
    letter-spacing: 0.06em;
    text-transform: uppercase;
    white-space: nowrap;
  }
  .card--front .wordmark__square { background: var(--white); }
  .card--front .wordmark__name { color: var(--white); }
  .card--front .website {
    margin-top: 38px;
    font-family: "Jost", sans-serif;
    font-size: 17px;
    letter-spacing: 0.03em;
  }
  .card--back .wordmark {
    position: absolute;
    left: 36px;
    top: 120px;
    width: 280px;
    gap: 18px;
  }
  .card--back .wordmark__square { background: var(--navy); width: 52px; height: 52px; }
  .card--back .wordmark__name { color: var(--ink); font-size: 27px; }
  .divider {
    position: absolute;
    left: 336px;
    top: 118px;
    width: 2px;
    height: 170px;
    background: var(--rule);
  }
  .contact {
    position: absolute;
    left: 358px;
    top: 80px;
    font-family: "Jost", sans-serif;
    font-size: 16px;
    line-height: 1.35;
  }
  .contact__name {
    position: relative;
    font-weight: 700;
    font-size: 23px;
    color: var(--navy);
    text-transform: uppercase;
    letter-spacing: 0.01em;
    line-height: 1.1;
  }
  .contact__name::before {
    content: "";
    position: absolute;
    left: -14px;
    top: 0;
    width: 3px;
    height: 30px;
    background: var(--navy);
  }
  .contact__title { font-size: 17px; margin-bottom: 10px; }
  .contact__address { margin-bottom: 12px; }
  .contact__label { font-weight: 700; color: var(--navy); margin-right: 4px; }
  .contact__row { display: flex; align-items: center; gap: 7px; }
  .contact__icon { width: 15px; height: 15px; flex: none; }
  .contact__web strong { font-weight: 700; color: var(--navy); }
</style>
</head>
<body>
<main class="canvas">
  <section class="card card--front" aria-label="Card front">
    <div class="wordmark">
      <span class="wordmark__square" aria-hidden="true"></span>
      <span class="wordmark__name">Quayview Legal</span>
    </div>
    <p class="website">www.qvlegal.com.au</p>
  </section>

  <section class="card card--back" aria-label="Card back">
    <div class="wordmark">
      <span class="wordmark__square" aria-hidden="true"></span>
      <span class="wordmark__name">Quayview Legal</span>
    </div>
    <span class="divider" aria-hidden="true"></span>
    <div class="contact">
      <p class="contact__name">Paul Whitcombe</p>
      <p class="contact__title">Managing Partner</p>
      <p class="contact__address">Level 9, 7 Ferris Lane<br>Sydney NSW 2000</p>
      <p><span class="contact__label">Main Tel</span>02 9364 2710</p>
      <p><span class="contact__label">Direct Tel</span>02 8472 3159</p>
      <p class="contact__row">
        <svg class="contact__icon" viewBox="0 0 16 16" aria-hidden="true">
          <rect x="1" y="3" width="14" height="10" rx="1.5" fill="var(--navy)"/>
          <path d="M1.5 4 L8 9 L14.5 4" fill="none" stroke="var(--white)" stroke-width="1.3"/>
        </svg>
        paul@qvlegal.com.au
      </p>
      <p class="contact__row contact__web">
        <svg class="contact__icon" viewBox="0 0 16 16" aria-hidden="true">
          <circle cx="8" cy="8" r="7" fill="var(--navy)"/>
          <g fill="none" stroke="var(--white)" stroke-width="0.9">
            <ellipse cx="8" cy="8" rx="3" ry="7"/>
            <line x1="1" y1="8" x2="15" y2="8"/>
            <line x1="2.2" y1="4.5" x2="13.8" y2="4.5"/>
            <line x1="2.2" y1="11.5" x2="13.8" y2="11.5"/>
          </g>
        </svg>
        <span>www.<strong>qvlegal.com</strong>.au</span>
      </p>
    </div>
  </section>
</main>
</body>
</html>
```